Redesign of business card for Cedar Ridge Mechanical

We are looking for a new design for our business cards for Cedar Ridge Mechanical. We are a plumbing & HVAC construction company, operating on the West Coast of Canada and USA. Logo attached.
Industry/Entity Type
Construction - Plumbing & HVAC
Contact Information for Business Card
Name, address, phone numbers, email, website address
Look and feel
Each slider illustrates characteristics of the customer's brand and the style your logo design should communicate.

```html
<!DOCTYPE html>
<html lang="en">
<head>
<meta charset="UTF-8">
<title>Cedar Ridge Mechanical – Business Card</title>
<link rel="stylesheet" href="https://fonts.googleapis.com/css2?family=Open+Sans:wght@400;600;700&family=Montserrat:wght@400&display=swap">
<style>
  :root {
    --page-bg: #e9e4dd;
    --card-face: #efebe5;
    --card-edge: #d9d2c8;
    --band-dark: #1b1917;
    --band-mid: #2d2a27;
    --ink: #1f1d1b;
    --gold-name: #cdbba4;
    --gold-text: #dccfbe;
  }
  html, body {
    margin: 0;
    padding: 0;
    width: 1200px;
    height: 1047px;
    overflow: hidden;
    background: var(--page-bg);
  }
  .business-card {
    position: absolute;
    left: 160px;
    top: 283px;
    width: 880px;
    height: 480px;
    border-radius: 22px;
    overflow: hidden;
    background: var(--card-face);
    box-shadow: 0 0 0 1px var(--card-edge), 0 14px 36px rgba(0,0,0,0.12);
    font-family: "Open Sans", sans-serif;
  }
  .lower-band {
    position: absolute;
    inset: 0;
  }
  .brand-block {
    position: absolute;
    right: 38px;
    top: 40px;
    width: 330px;
    display: flex;
    align-items: center;
    gap: 18px;
  }
  .brand-square {
    width: 40px;
    height: 40px;
    flex: none;
    background: var(--ink);
  }
  .brand-name {
    margin: 0;
    font-weight: 700;
    font-size: 36px;
    line-height: 1.12;
    letter-spacing: 0.5px;
    color: var(--ink);
    text-transform: uppercase;
  }
  .person {
    position: absolute;
    left: 38px;
    top: 232px;
  }
  .person-name {
    margin: 0;
    font-weight: 700;
    font-size: 31px;
    letter-spacing: 0.6px;
    color: var(--gold-name);
    line-height: 1.2;
  }
  .person-title {
    margin: 2px 0 0;
    font-weight: 400;
    font-size: 21px;
    color: var(--gold-name);
  }
  .contact-list {
    position: absolute;
    left: 34px;
    top: 335px;
    margin: 0;
    padding: 0;
    list-style: none;
    font-family: "Montserrat", sans-serif;
    font-size: 22px;
    color: var(--gold-text);
  }
  .contact-list li {
    display: flex;
    align-items: center;
    gap: 8px;
    height: 32px;
  }
  .contact-list svg {
    width: 20px;
    height: 20px;
    fill: none;
    stroke: var(--gold-text);
    stroke-width: 1.8;
  }
  .address {
    position: absolute;
    right: 36px;
    top: 367px;
    margin: 0;
    text-align: right;
    font-style: normal;
    font-family: "Montserrat", sans-serif;
    font-size: 22px;
    line-height: 32px;
    color: var(--gold-text);
  }
</style>
</head>
<body>
  <div class="business-card">
    <svg class="lower-band" viewBox="0 0 880 480" preserveAspectRatio="none" aria-hidden="true">
      <defs>
        <linearGradient id="bandShade" x1="0" y1="0" x2="1" y2="1">
          <stop offset="0" stop-color="var(--band-mid)"/>
          <stop offset="1" stop-color="var(--band-dark)"/>
        </linearGradient>
      </defs>
      <path d="M0,210 C260,170 520,320 880,265 L880,480 L0,480 Z" fill="url(#bandShade)"/>
    </svg>

    <div class="brand-block">
      <span class="brand-square" aria-hidden="true"></span>
      <p class="brand-name">Cedar Ridge Mechanical</p>
    </div>

    <div class="person">
      <h1 class="person-name">DANIEL HAYES</h1>
      <p class="person-title">Managing Director</p>
    </div>

    <ul class="contact-list">
      <li>
        <svg viewBox="0 0 24 24" aria-hidden="true"><path d="M5 3h4l2 5-3 2a11 11 0 0 0 6 6l2-3 5 2v4a2 2 0 0 1-2 2A18 18 0 0 1 3 5a2 2 0 0 1 2-2z"/></svg>
        <span>123 456 789</span>
      </li>
      <li>
        <svg viewBox="0 0 24 24" aria-hidden="true"><rect x="3" y="6" width="18" height="13" rx="1"/><path d="M3 7l9 7 9-7"/></svg>
        <span>info@yourgmail.com</span>
      </li>
      <li>
        <svg viewBox="0 0 24 24" aria-hidden="true"><circle cx="12" cy="12" r="9"/><path d="M3 12h18M12 3c3 3 3 15 0 18M12 3c-3 3-3 15 0 18"/></svg>
        <span>www.yourwebsite.com</span>
      </li>
    </ul>

    <address class="address">Your address, City<br>State, Zip 1234</address>
  </div>
</body>
</html>
```